VENTURE CAPITAL GROUP BUSINESS CARD DESIGN

Venture Capital Group based in SF looking for a bold business card design. No trendy colour explosion, 3D effects etc. Just "simple" optical effects. Works on your brain, keeps your eye focused and sticks to your mind.
Target Market(s)
Technology startups
Industry/Entity Type
Venture Capital
Contact Information for Business Card
DESMOND WHITLAKE
MANAGING PARTNER
187 FENWORTH ST SAN FRANCISCO, CA 94187
415.555.0142 O
415.555.0147 F
415.555.0193 C
desmond@veldtmoorcapital.ventures

```html
<!DOCTYPE html>
<html lang="en">
<head>
<meta charset="utf-8">
<title>Veldtmoor Capital Group — Business Card</title>
<link href="https://fonts.googleapis.com/css2?family=Merriweather:wght@400;700&family=Source+Sans+3:wght@400&display=swap" rel="stylesheet">
<style>
  :root {
    --backdrop: #a7a4a5;
    --paper: #fbfbfb;
    --green: #1f8a3a;
    --green-light: #3cb44f;
    --green-dark: #16702c;
    --ink: #5b5b5b;
    --ink-soft: #6e6e6e;
    --rule: #e4e4e4;
    --silver-light: #c4c4c6;
    --silver-dark: #8a8a8c;
  }
  * { margin: 0; padding: 0; box-sizing: border-box; }
  html, body { width: 1200px; height: 1200px; overflow: hidden; }
  body { background: var(--backdrop); position: relative; font-family: "Source Sans 3", sans-serif; }

  .card {
    position: absolute;
    width: 713px;
    height: 418px;
    background: var(--paper);
    overflow: hidden;
  }
  .card--front { left: 238px; top: 118px; }
  .card--back  { left: 230px; top: 644px; }

  /* Brand lockup: company name set in the card's own serif */
  .brand {
    position: absolute;
    text-align: center;
    color: var(--green);
    font-family: "Merriweather", serif;
    font-weight: 700;
    line-height: 1.25;
  }
  .brand__line { display: block; }

  .card--front .brand { left: 0; right: 0; top: 160px; font-size: 40px; }
  .card--back .brand { left: 20px; width: 290px; top: 160px; font-size: 30px; }

  .divider {
    position: absolute; left: 326px; top: 60px; width: 1px; height: 250px;
    background: var(--rule);
  }

  .person { position: absolute; left: 360px; top: 96px; }
  .person__name { font-family: "Merriweather", serif; font-weight: 700; font-size: 25px; color: var(--ink); letter-spacing: 0.3px; }
  .person__title { font-family: "Merriweather", serif; font-size: 16px; color: var(--ink-soft); margin-top: 2px; }

  .contact { position: absolute; left: 360px; top: 180px; list-style: none; }
  .contact__item { display: flex; align-items: center; height: 23.5px; font-size: 18.5px; color: var(--ink); }
  .contact__icon { width: 18px; height: 16px; margin-right: 17px; fill: var(--green); flex: none; }
  .address { position: absolute; left: 360px; top: 276px; font-size: 18.5px; color: var(--ink); }

  .band-silver {
    position: absolute; left: 0; bottom: 0; width: 330px; height: 27px;
    background: linear-gradient(90deg, var(--silver-light), var(--silver-dark));
  }
  .band-green {
    position: absolute; right: 0; bottom: 0; width: 420px; height: 53px;
    background: linear-gradient(90deg, var(--green-light), var(--green-dark));
    clip-path: polygon(40px 0, 100% 0, 100% 100%, 0 100%);
  }
  .website {
    position: absolute; left: 360px; bottom: 14px;
    font-size: 18.5px; color: #ffffff; letter-spacing: 0.2px;
  }
</style>
</head>
<body>

  <section class="card card--front" aria-label="Card front">
    <div class="brand">
      <span class="brand__line">Veldtmoor</span>
      <span class="brand__line">Capital Group</span>
    </div>
  </section>

  <section class="card card--back" aria-label="Card back">
    <div class="brand">
      <span class="brand__line">Veldtmoor</span>
      <span class="brand__line">Capital Group</span>
    </div>

    <div class="divider"></div>

    <div class="person">
      <div class="person__name">Desmond Whitlake</div>
      <div class="person__title">Managing Partner</div>
    </div>

    <ul class="contact">
      <li class="contact__item">
        <svg class="contact__icon" viewBox="0 0 18 16" aria-hidden="true"><path d="M1 5 C1 2 5 1 9 1 C13 1 17 2 17 5 L13 6 L12 4 H6 L5 6 Z M4 8 L6 6 H12 L14 8 V15 H4 Z"/></svg>
        415.555.0142
      </li>
      <li class="contact__item">
        <svg class="contact__icon" viewBox="0 0 18 16" aria-hidden="true"><path d="M4 1 H14 V5 H4 Z M1 6 H17 V12 H14 V10 H4 V12 H1 Z M5 11 H13 V15 H5 Z"/></svg>
        415.555.0147
      </li>
      <li class="contact__item">
        <svg class="contact__icon" viewBox="0 0 18 16" aria-hidden="true"><path d="M5 0 H13 V16 H5 Z M6.5 2 V12 H11.5 V2 Z" fill-rule="evenodd"/></svg>
        415.555.0193
      </li>
      <li class="contact__item">
        <svg class="contact__icon" viewBox="0 0 18 16" aria-hidden="true"><path d="M1 3 H17 V13 H1 Z M2.5 4 L9 9 L15.5 4 Z" fill-rule="evenodd"/></svg>
        desmond@veldtmoorcapital.ventures
      </li>
    </ul>

    <div class="address">187 Fenworth St San Francisco, CA 94187</div>

    <div class="band-silver"></div>
    <div class="band-green"></div>
    <div class="website">www.veldtmoorcapital.ventures</div>
  </section>

</body>
</html>
```